Indy Film Production Company/Studio

We need a business card designed from an existing logo. We are a digital studio/production company that caters to creating genre entertainment, like Action, Horror, and martial arts. The card along with the logo will be used to Brand the company from letter heads to banners. The design will also be used for postcards and Brochures. It should be professional and masculine.
Updates

Thank you to all the designers who have participated. I'm narrowing down who it will be. Thank you again.

Target Market(s)

Investors, Networks, Producers, and actors

Industry/Entity Type

Film Production

Contact Information for Business Card

Teodoro Valbuena
Producer/Writer/Director
www.kestrelpicturehouse.example

Requirements
Must have
• Website address, Facebook icon and Twitter icon possibly in the back of the card.
Nice to have
• Logline of Company: Follow The Action.

```html
<!DOCTYPE html>
<html lang="en">
<head>
<meta charset="utf-8">
<title>Kestrel Picture House – Business Card</title>
<link rel="stylesheet" href="https://fonts.googleapis.com/css2?family=Oswald:wght@600&family=Roboto+Condensed:wght@300;400&display=swap">
<style>
  :root {
    --stage: #dcd7d1;
    --card-paper: #f3f1ee;
    --brand-red: #d2232a;
    --band-red-top: #e0262d;
    --band-red-bottom: #a9151b;
    --panel-black: #121212;
    --panel-black-edge: #262626;
    --name-ink: #f1e9e6;
    --title-ink: #e9bcbc;
    --contact-ink: #cdbfa9;
  }
  html, body {
    margin: 0;
    padding: 0;
    width: 1200px;
    height: 969px;
    overflow: hidden;
    background: var(--stage);
  }
  .canvas {
    position: relative;
    width: 1200px;
    height: 969px;
  }
  .business-card {
    position: absolute;
    left: 100px;
    top: 201px;
    width: 1000px;
    height: 567px;
    background: var(--card-paper);
    border-radius: 6px;
    overflow: hidden;
    box-shadow: 0 18px 40px rgba(0,0,0,0.22);
  }
  .card-shapes {
    position: absolute;
    inset: 0;
  }
  .brand-name {
    position: absolute;
    left: 46px;
    top: 86px;
    margin: 0;
    font-family: "Oswald", sans-serif;
    font-weight: 600;
    color: var(--brand-red);
    text-transform: uppercase;
    line-height: 1;
  }
  .brand-name .brand-main {
    display: block;
    font-size: 132px;
    letter-spacing: 2px;
  }
  .brand-name .brand-sub {
    display: block;
    font-size: 41px;
    letter-spacing: 3px;
    margin-top: 10px;
  }
  .person {
    position: absolute;
    left: 34px;
    top: 443px;
    font-family: "Roboto Condensed", sans-serif;
    font-style: italic;
    text-transform: uppercase;
  }
  .person-name {
    margin: 0;
    font-size: 31px;
    font-weight: 400;
    letter-spacing: 1px;
    color: var(--name-ink);
  }
  .person-role {
    margin: 6px 0 0;
    font-size: 22px;
    font-weight: 300;
    letter-spacing: 1px;
    color: var(--title-ink);
  }
  .social {
    position: absolute;
    right: 38px;
    top: 350px;
    display: flex;
    gap: 8px;
  }
  .social-dot {
    width: 44px;
    height: 44px;
    border: 2px solid var(--contact-ink);
    border-radius: 50%;
    box-sizing: border-box;
  }
  .contact-list {
    position: absolute;
    right: 38px;
    top: 420px;
    margin: 0;
    padding: 0;
    list-style: none;
    font-family: "Roboto Condensed", sans-serif;
    font-style: italic;
    font-weight: 300;
    font-size: 24px;
    color: var(--contact-ink);
    text-align: right;
  }
  .contact-list li {
    display: flex;
    justify-content: flex-end;
    align-items: center;
    gap: 12px;
    height: 38px;
  }
  .contact-list svg {
    width: 24px;
    height: 24px;
    flex: none;
    fill: var(--contact-ink);
  }
</style>
</head>
<body>
<main class="canvas">
  <article class="business-card">
    <svg class="card-shapes" viewBox="0 0 1000 567" width="1000" height="567" aria-hidden="true">
      <defs>
        <linearGradient id="bandRed" x1="0" y1="0" x2="0" y2="1">
          <stop offset="0" stop-color="var(--band-red-top)"/>
          <stop offset="1" stop-color="var(--band-red-bottom)"/>
        </linearGradient>
        <linearGradient id="panelBlack" x1="0" y1="0" x2="1" y2="1">
          <stop offset="0" stop-color="var(--panel-black-edge)"/>
          <stop offset="1" stop-color="var(--panel-black)"/>
        </linearGradient>
      </defs>
      <rect class="red-band" x="0" y="380" width="720" height="187" fill="url(#bandRed)"/>
      <polygon class="black-panel" points="1000,0 1000,567 418,567 992,0" fill="url(#panelBlack)"/>
    </svg>

    <h1 class="brand-name">
      <span class="brand-main">Kestrel</span>
      <span class="brand-sub">Picture House</span>
    </h1>

    <div class="person">
      <p class="person-name">Teodoro Valbuena</p>
      <p class="person-role">Producer/Writer/Director</p>
    </div>

    <div class="social" aria-label="Social profiles">
      <span class="social-dot"></span>
      <span class="social-dot"></span>
    </div>

    <ul class="contact-list">
      <li>555 0147 2290
        <svg viewBox="0 0 24 24" aria-hidden="true"><path d="M6.6 10.8a15.1 15.1 0 0 0 6.6 6.6l2.2-2.2a1 1 0 0 1 1-.25 11.4 11.4 0 0 0 3.6.57 1 1 0 0 1 1 1V20a1 1 0 0 1-1 1A17 17 0 0 1 3 4a1 1 0 0 1 1-1h3.5a1 1 0 0 1 1 1c0 1.25.2 2.45.57 3.57a1 1 0 0 1-.25 1z"/></svg>
      </li>
      <li>teo@kestrelpicturehouse.example
        <svg viewBox="0 0 24 24" aria-hidden="true"><path d="M2 5h20v14H2z M3.5 6.5 12 13l8.5-6.5" fill="none" stroke="var(--contact-ink)" stroke-width="0"/><path d="M2 5h20v2l-10 7L2 7z"/><path d="M2 9l10 7 10-7v10H2z"/></svg>
      </li>
      <li>www.kestrelpicturehouse.example
        <svg viewBox="0 0 24 24" aria-hidden="true"><circle cx="12" cy="12" r="9.5" fill="none" stroke="var(--contact-ink)" stroke-width="2"/><ellipse cx="12" cy="12" rx="4" ry="9.5" fill="none" stroke="var(--contact-ink)" stroke-width="1.6"/><path d="M2.5 12h19M4 7h16M4 17h16" stroke="var(--contact-ink)" stroke-width="1.4"/></svg>
      </li>
    </ul>
  </article>
</main>
</body>
</html>
```